Whitcombe Business Card Design

The name of the business is Dario Whitcombe, CPA LLC
The service that we offer is Accounting, Tax & Consulting Services. I need it to have the following items:
Dario Whitcombe, Principal
Phone Number
Email Address
Physical Address

I have attached the company logo, one in black and one in white. Please provide a design in black background and the other in white background. Please include "Accounting, Tax & Consulting Services". I want the business card to be clean and very professional.

```html
<!DOCTYPE html>
<html lang="en">
<head>
<meta charset="utf-8">
<title>Dario Whitcombe, CPA LLC — Business Cards</title>
<link rel="stylesheet" href="https://fonts.googleapis.com/css2?family=Montserrat:wght@600;700&family=Roboto:wght@300;400&display=swap">
<style>
  :root {
    --backdrop: #2b2b2b;
    --card-dark: #232324;
    --card-dark-edge: #2c2c2e;
    --card-light: #f4f4f2;
    --card-light-edge: #e6e6e4;
    --red: #8f1b1d;
    --white: #f2f2f2;
    --grey: #a9a9ab;
    --ink: #232324;
  }
  * { margin: 0; padding: 0; box-sizing: border-box; }
  html, body {
    width: 1200px;
    height: 1138px;
    overflow: hidden;
    background: var(--backdrop);
  }
  .card {
    position: absolute;
    left: 273px;
    width: 621px;
    height: 376px;
    border-radius: 16px;
  }
  .card--light {
    top: 184px;
    background: linear-gradient(160deg, var(--card-light) 0%, var(--card-light-edge) 100%);
  }
  .card--dark {
    top: 606px;
    background: linear-gradient(160deg, var(--card-dark) 0%, var(--card-dark-edge) 100%);
  }

  .front-mark {
    position: absolute;
    inset: 0;
    display: flex;
    flex-direction: column;
    align-items: center;
    justify-content: center;
    gap: 14px;
    font-family: "Montserrat", sans-serif;
  }
  .front-mark-name {
    display: flex;
    align-items: center;
    gap: 14px;
    font-weight: 700;
    font-size: 34px;
    letter-spacing: 3px;
    color: var(--ink);
  }
  .front-mark-name .square {
    width: 24px;
    height: 24px;
    background: var(--red);
  }
  .front-mark-tagline {
    font-weight: 600;
    font-size: 12px;
    letter-spacing: 2.4px;
    color: #6d6d70;
  }

  .firm {
    position: absolute;
    left: 36px;
    top: 52px;
    font-family: "Montserrat", sans-serif;
  }
  .firm-name {
    font-weight: 600;
    font-size: 22px;
    letter-spacing: 0.5px;
    color: var(--white);
    line-height: 1;
  }
  .firm-tagline {
    margin-top: 7px;
    font-weight: 600;
    font-size: 13px;
    letter-spacing: 1.6px;
    color: var(--grey);
  }

  .person {
    position: absolute;
    right: 33px;
    top: 152px;
    text-align: right;
  }
  .person-name {
    font-family: "Montserrat", sans-serif;
    font-weight: 700;
    font-size: 21px;
    letter-spacing: 0.5px;
    color: var(--red);
    line-height: 1;
  }
  .person-role {
    margin-top: 5px;
    font-family: "Roboto", sans-serif;
    font-weight: 400;
    font-size: 16px;
    color: var(--white);
  }

  .contact {
    position: absolute;
    right: 33px;
    top: 224px;
    text-align: right;
    font-family: "Roboto", sans-serif;
    font-weight: 300;
    font-size: 16px;
    line-height: 24px;
    color: var(--white);
    list-style: none;
  }
  .contact li { display: flex; justify-content: flex-end; align-items: center; gap: 8px; }
  .contact .line-gap { margin-top: 4px; }
  .contact svg { width: 14px; height: 14px; fill: var(--red); flex: none; }

  .back-mark {
    position: absolute;
    left: 36px;
    bottom: 36px;
    display: flex;
    align-items: center;
    gap: 10px;
    font-family: "Montserrat", sans-serif;
    font-weight: 600;
    font-size: 18px;
    letter-spacing: 1px;
    color: var(--white);
  }
  .back-mark .square {
    width: 16px;
    height: 16px;
    background: var(--red);
  }
</style>
</head>
<body>
  <section class="card card--light">
    <div class="front-mark">
      <p class="front-mark-name"><span class="square"></span>WHITCOMBE</p>
      <p class="front-mark-tagline">ACCOUNTING, TAX &amp; CONSULTING SERVICES</p>
    </div>
  </section>

  <section class="card card--dark">
    <div class="firm">
      <p class="firm-name">DARIO WHITCOMBE, CPA LLC</p>
      <p class="firm-tagline">ACCOUNTING, TAX &amp; CONSULTING SERVICES</p>
    </div>

    <div class="person">
      <p class="person-name">DARIO WHITCOMBE</p>
      <p class="person-role">Principal</p>
    </div>

    <ul class="contact">
      <li>418 Linden Row, Suite 3, Brookhaven,</li>
      <li>Greenfield County, US 204517</li>
      <li class="line-gap">555-204-3178
        <svg viewBox="0 0 16 16" aria-hidden="true"><path d="M3 2h3l1.5 3.5-2 1.2a8 8 0 0 0 3.8 3.8l1.2-2L14 10v3a1 1 0 0 1-1 1A11 11 0 0 1 2 3a1 1 0 0 1 1-1z"/></svg>
      </li>
      <li>dw@whitcombecpa.com
        <svg viewBox="0 0 16 16" aria-hidden="true"><path d="M1 3h14v10H1z M1.8 3.6 8 8.6l6.2-5" stroke="#232324" stroke-width="1.2"/></svg>
      </li>
      <li>www.whitcombecpa.com
        <svg viewBox="0 0 16 16" aria-hidden="true"><circle cx="8" cy="8" r="7"/><path d="M1 8h14M8 1c-3 3.5-3 10.5 0 14M8 1c3 3.5 3 10.5 0 14" stroke="#232324" stroke-width="1" fill="none"/></svg>
      </li>
    </ul>

    <div class="back-mark"><span class="square"></span>WHITCOMBE</div>
  </section>
</body>
</html>
```